Ledgerline Code Works business card design.

We are a software development company that develop Software for finance companies and related industries.

We need a 2 sided business card designed. We have a new logo already designed (see attached eps and ai) We are after a clean simple corporate look. One side with just our logo, and the second side with our details.

Greg Halvorsen
Managing Director

Suite 5 Level 8, 147 Marlow Street Sydney NSW 2000

Direct: +61 2 9387 4625
Mobile: +61 4 1736 8490
Email: gregh@lcw.net.au
Web: www.lcw.net.au

I have included 2 logo files an .ai and .eps. I noticed that the lines either side of the partners looks a bit jaggered and needs to be made sharper.

I would like to introduce a little colour somewhere rather than having it all black and white. But not over the top, keeping with a simple clean corporate look. Perhaps a light blue on some of the text?

If you have other ideas would be pleased to review

Regards

Greg H.

```html
<!DOCTYPE html>
<html lang="en">
<head>
<meta charset="utf-8">
<title>Ledgerline Code Works – Business Card</title>
<link href="https://fonts.googleapis.com/css2?family=Open+Sans:wght@400;600;700&display=swap" rel="stylesheet">
<style>
  :root {
    --backdrop: #e9e6e2;
    --card-black: #0b0b0c;
    --card-sheen: #2a2a2d;
    --accent-blue: #7cc4ec;
    --accent-blue-deep: #5aaee0;
    --band-text: #14324a;
    --white: #ffffff;
    --rule: #8a8a8e;
  }
  * { margin: 0; padding: 0; box-sizing: border-box; }
  html, body {
    width: 1200px; height: 913px; overflow: hidden;
    background: var(--backdrop);
    font-family: "Open Sans", Arial, sans-serif;
  }
  .canvas { position: relative; width: 1200px; height: 913px; }

  .card {
    position: absolute;
    width: 630px; height: 360px;
    border-radius: 6px;
    overflow: hidden;
    background: linear-gradient(135deg, var(--card-sheen) 0%, var(--card-black) 45%, var(--card-black) 100%);
    box-shadow: 0 14px 30px rgba(0,0,0,.28);
  }
  .card--front { left: 90px; top: 70px; }
  .card--back { left: 480px; top: 483px; }

  .wordmark { position: absolute; text-align: center; color: var(--white); }
  .wordmark__name {
    font-weight: 700; font-size: 30px; letter-spacing: 1px;
    text-transform: uppercase; white-space: nowrap;
  }
  .wordmark__rule { height: 1px; background: var(--rule); margin-top: 8px; }
  .card--front .wordmark { left: 0; right: 0; top: 158px; }
  .card--front .wordmark__rule { width: 420px; margin-left: auto; margin-right: auto; }
  .card--back .wordmark { left: 40px; width: 400px; top: 118px; }
  .card--back .wordmark__name { font-size: 23px; }

  .band { position: absolute; left: 0; top: 0; width: 630px; height: 360px; }

  .holder { position: absolute; right: 28px; top: 168px; text-align: right; }
  .holder__name { color: var(--accent-blue); font-weight: 700; font-size: 17px; }
  .holder__title { color: var(--white); font-size: 12px; }

  .contacts {
    position: absolute; left: 22px; top: 266px;
    color: var(--band-text); font-size: 13px; line-height: 26px;
  }
  .contacts__row { display: flex; align-items: center; gap: 8px; white-space: nowrap; }
  .contacts__item { display: inline-flex; align-items: center; gap: 7px; margin-right: 16px; }
  .icon { width: 13px; height: 13px; fill: var(--band-text); flex: none; }
</style>
</head>
<body>
<div class="canvas">

  <section class="card card--front" aria-label="Card front">
    <div class="wordmark">
      <div class="wordmark__name">Ledgerline Code Works</div>
      <div class="wordmark__rule"></div>
    </div>
  </section>

  <section class="card card--back" aria-label="Card back">
    <svg class="band" viewBox="0 0 630 360" aria-hidden="true">
      <polygon points="0,252 330,252 352,222 630,222 630,360 0,360" fill="var(--accent-blue)"/>
      <polygon points="0,352 630,352 630,360 0,360" fill="var(--accent-blue-deep)"/>
    </svg>

    <div class="wordmark">
      <div class="wordmark__name">Ledgerline Code Works</div>
      <div class="wordmark__rule"></div>
    </div>

    <div class="holder">
      <div class="holder__name">Greg Halvorsen</div>
      <div class="holder__title">Managing Director</div>
    </div>

    <div class="contacts">
      <div class="contacts__row">
        <span class="contacts__item">
          <svg class="icon" viewBox="0 0 16 16"><path d="M3 1h3l1.5 4-2 1.5a9 9 0 0 0 4 4L11 8.5l4 1.5v3c0 1-1 2-2 2A13 13 0 0 1 1 3c0-1 1-2 2-2z"/></svg>
          +61 2 9387 4625
        </span>
        <span class="contacts__item">
          <svg class="icon" viewBox="0 0 16 16"><path d="M4 0h8a1 1 0 0 1 1 1v14a1 1 0 0 1-1 1H4a1 1 0 0 1-1-1V1a1 1 0 0 1 1-1zm1 2v10h6V2zm3 11a1 1 0 1 0 0 2 1 1 0 0 0 0-2z"/></svg>
          +61 4 1736 8490
        </span>
      </div>
      <div class="contacts__row">
        <span class="contacts__item">
          <svg class="icon" viewBox="0 0 16 16"><path d="M0 3h16v10H0zm1.5 1.2V5l6.5 4 6.5-4v-.8z"/></svg>
          gregh@lcw.net.au
        </span>
        <span class="contacts__item">
          <svg class="icon" viewBox="0 0 16 16"><path d="M8 0a8 8 0 1 0 0 16A8 8 0 0 0 8 0zm0 1.5c1 1.2 1.7 3 1.9 5.5H6.1C6.3 4.5 7 2.7 8 1.5zM1.6 9h3c.1 2 .6 3.7 1.4 5A6.5 6.5 0 0 1 1.6 9zm0-2A6.5 6.5 0 0 1 6 2c-.8 1.3-1.3 3-1.4 5zm4.5 2h3.8c-.2 2.5-.9 4.3-1.9 5.5-1-1.2-1.7-3-1.9-5.5zm5.3 0h3A6.5 6.5 0 0 1 10 14c.8-1.3 1.3-3 1.4-5zm0-2c-.1-2-.6-3.7-1.4-5a6.5 6.5 0 0 1 4.4 5z"/></svg>
          Web: www.lcw.net.au
        </span>
      </div>
      <div class="contacts__row">
        <span class="contacts__item">
          <svg class="icon" viewBox="0 0 16 16"><path d="M8 0a5.5 5.5 0 0 0-5.5 5.5C2.5 10 8 16 8 16s5.5-6 5.5-10.5A5.5 5.5 0 0 0 8 0zm0 7.7a2.2 2.2 0 1 1 0-4.4 2.2 2.2 0 0 1 0 4.4z"/></svg>
          Suite 5 Level 8, 147 Marlow Street Sydney NSW 2000
        </span>
      </div>
    </div>
  </section>

</div>
</body>
</html>
```